Business card for Crestline Bathrooms

Please design a business card for our bathroom renovation business. You can use my existing logo, but if you have an idea to modernize it, I would like to see it. Please see attached files first. I would like to use the blue and the orange theme. I like the concept of using the shower head in the logo. Please find following a design (or two) that I have been trying to create with my limited resources. That design was for a sign, but I was going to adopt it and use it as a business card as well. I like the concept of the water splash but I don’t think it “flows” nicely together with the logo. Another thought is that maybe creating the logo out of water splash could work and have a dramatic effect (like the water text and the butterfly picture attached with similar background instead of white). If the above doesn’t work I would like to see a modern simplified design. One of the attached files named as the unwanted business card has all the details that I want included in the business card. Please note that it is two sided.
Updates

I am very thankful for the designs that I have received, but they are very similar and only a couple of attempts to do something with the water splash as per my original brief. Modernizing the logo and having it made out of out of water splash with the orange as color accent could work and have a dramatic effect (like the water text and the butterfly picture attached with similar background instead of white). Please do not use the butterfly itself! This is just an example that images can be created out of water splash.

Contact Information for Business Card

all the details are on the unwonted business card file included

Colors
3176b5

Requirements
Nice to have
• Copied from the brief:
• ... maybe creating the logo out of water splash could work and have a dramatic effect (like the water text and the butterfly picture attached with similar background instead of white). Please do not use the butterfly itself!
Should not have
• I am getting designs with a butterfly. The butterfly picture was an example of creating something from a water splash. The butterfly itself has no association with anything other than the concept of creating a logo out of water splash. Sorry, I thought I was clear in the brief.

```html
<!DOCTYPE html>
<html lang="en">
<head>
<meta charset="utf-8">
<title>Crestline Bathrooms – Business Card</title>
<link href="https://fonts.googleapis.com/css2?family=Arimo:wght@400;700&display=swap" rel="stylesheet">
<style>
  :root {
    --navy: #0d4069;
    --coral: #ec7f6c;
    --paper: #f4f4f5;
    --ink-light: #ffffff;
    --badge-green: #2fae3c;
    --backdrop: #e7e4e1;
  }
  * { margin: 0; padding: 0; box-sizing: border-box; }
  html, body {
    width: 1200px; height: 900px; overflow: hidden;
    background: var(--backdrop);
    font-family: "Arimo", Arial, sans-serif;
  }
  .card {
    position: absolute; left: 120px; top: 155px;
    width: 960px; height: 590px;
    background: var(--paper);
    box-shadow: 0 10px 30px rgba(0,0,0,.18);
    overflow: hidden;
  }
  .card__wave { position: absolute; inset: 0; }
  .contact { position: absolute; left: 40px; top: 60px; color: var(--ink-light); }
  .contact__name {
    color: var(--coral); font-weight: 700; font-size: 32px;
    letter-spacing: .5px; margin-bottom: 18px;
  }
  .contact__list { list-style: none; }
  .contact__item {
    display: flex; align-items: center; gap: 10px;
    font-size: 25px; line-height: 35px;
  }
  .contact__icon { width: 20px; height: 20px; flex: none; }
  .contact__address { font-size: 25px; margin: 14px 0 0 8px; }
  .services { list-style: none; margin-top: 32px; }
  .services__item {
    position: relative; padding-left: 18px;
    font-size: 22px; line-height: 30px;
  }
  .services__item::before {
    content: ""; position: absolute; left: 0; top: 10px;
    width: 11px; height: 11px; border-radius: 50%; background: var(--coral);
  }
  .brand {
    position: absolute; left: 572px; top: 240px; width: 350px;
    text-align: center; color: var(--navy); font-weight: 400;
  }
  .brand__name { font-size: 66px; line-height: 1; letter-spacing: 1px; }
  .brand__sub { font-size: 30px; letter-spacing: 3px; margin-top: 8px; }
  .badges { position: absolute; left: 533px; top: 462px; display: flex; gap: 30px; align-items: center; }
  .badge--member { width: 64px; height: 72px; border-radius: 12px; background: var(--badge-green); }
  .badge--association { width: 290px; height: 56px; background: var(--navy); border-radius: 4px; }
</style>
</head>
<body>
  <section class="card" aria-label="Crestline Bathrooms business card">
    <svg class="card__wave" viewBox="0 0 960 590" width="960" height="590" aria-hidden="true">
      <path fill="var(--navy)" d="M0 0 H660 C585 0 540 40 530 110 C520 200 522 300 522 390 C522 480 430 565 300 590 H0 Z"/>
      <path fill="none" stroke="var(--coral)" stroke-width="4" d="M690 4 C600 4 556 48 545 112 C535 200 537 300 537 392 C537 490 445 574 320 590"/>
    </svg>

    <div class="contact">
      <h1 class="contact__name">DANIEL MAROVIC</h1>
      <ul class="contact__list">
        <li class="contact__item">
          <svg class="contact__icon" viewBox="0 0 20 20" aria-hidden="true"><path fill="var(--coral)" d="M2 7 C2 3 18 3 18 7 L15 9 L13 6 H7 L5 9 Z M5 10 H15 L17 17 H3 Z"/></svg>
          0400 555 218
        </li>
        <li class="contact__item">
          <svg class="contact__icon" viewBox="0 0 20 20" aria-hidden="true"><rect x="5" y="1" width="10" height="18" rx="2" fill="none" stroke="var(--coral)" stroke-width="2"/></svg>
          6200 4417
        </li>
        <li class="contact__item">
          <svg class="contact__icon" viewBox="0 0 20 20" aria-hidden="true"><rect x="2" y="4" width="16" height="12" fill="var(--coral)"/><path d="M2 4 L10 11 L18 4" fill="none" stroke="var(--navy)" stroke-width="1.5"/></svg>
          dan@crestlinebathrooms.com.au
        </li>
        <li class="contact__item">
          <svg class="contact__icon" viewBox="0 0 20 20" aria-hidden="true"><circle cx="10" cy="10" r="8" fill="var(--coral)"/><path d="M6 6 Q9 8 8 11 Q12 12 11 16 M13 4 Q12 7 15 8" fill="none" stroke="var(--navy)" stroke-width="1.5"/></svg>
          crestlinebathrooms.com.au
        </li>
      </ul>
      <p class="contact__address">PO Box 41 Larkfield 2620</p>
      <ul class="services">
        <li class="services__item">Complete bathroom renovations<br>and remodelling</li>
        <li class="services__item">Highly skilled &amp; qualified tradespeople</li>
        <li class="services__item">Professional service from concept<br>to completion</li>
        <li class="services__item">All work guaranteed</li>
      </ul>
    </div>

    <div class="brand">
      <div class="brand__name">Crestline</div>
      <div class="brand__sub">Bathrooms</div>
    </div>

    <div class="badges">
      <div class="badge badge--member" role="img" aria-label="Industry association membership badge"></div>
      <div class="badge badge--association" role="img" aria-label="Builders association membership badge"></div>
    </div>
  </section>
</body>
</html>
```